Welcome Card Project for bow tie business

We need a welcome message card that will be placed inside a box (packaging) for a mens bow tie business 'Dorian Vantle'. Dorian Vantle is a men's brand specializing in unique bow ties of limited editions using quality designer fabrics.
Dorian Vantle is all about colour, prints and style, where the consumer can add a something a little out of the ordinary and quirky to break out of the mundane 9-5 day.

The dimensions of the double sided welcome card is as follows:
60mm H x 120mm W

One side of the welcome card will have the welcome message with colour and graphics in the background depicting happiness and excitement. It will also include the Facebook, twitter and Instagram logos and an invitation for customers to share pictures of them wearing the bow ties on Instagram and facebook. The website address will also be included here (www.dorianvantle.example)

The other side of the welcome card will be more conservative with a black on black paisley print design with the 'Dorian Vantle' logo in a deep purple colour.

Target Market(s)

Men, hipsters, fashionistas, working professionals, women seeking gifts for men

Industry/Entity Type

Conservative

Requirements
Must have
• - Double sided welcome card
- The welcome message (file attached) on one side of the card
- Facebook + Instagram logo
- Dorian Vantle website address (www.dorianvantle.example)
- Corporate colours: purple, black, orange (on website and in logo) + neutral recycled brown (packaging colour)
- Black on black paisley print on one side of the card
- Dorian Vantle logo (file attached)- colour: deep purple
Nice to have

Should not have
• - pictures of rainbows

```html
<!DOCTYPE html>
<html lang="en">
<head>
<meta charset="utf-8">
<title>Dorian Vantle — Welcome Card</title>
<link rel="stylesheet" href="https://fonts.googleapis.com/css2?family=Crimson+Pro:wght@400;700&family=Great+Vibes&family=Roboto+Condensed:wght@700&family=Oswald:wght@600&display=swap">
<style>
  :root {
    --page: #ffffff;
    --border-tone: #e4566f;
    --border-deep: #c93e63;
    --panel-left: #ef4d68;
    --panel-mid: #ff6476;
    --panel-right: #ff3a60;
    --rule: #5a0b3e;
    --body-ink: #b31b53;
    --url-ink: #4a0a3a;
    --light: #ffffff;
    --ornament: #5a0b3e;
  }
  html, body { margin: 0; padding: 0; }
  body {
    width: 1115px; height: 1200px; overflow: hidden;
    background: var(--page); position: relative;
  }
  .card {
    position: absolute; left: 117px; width: 886px; height: 465px;
  }
  .card--message { top: 60px; }
  .card--brand { top: 638px; }
  .card__border {
    position: absolute; inset: 0;
    background: linear-gradient(90deg, var(--border-tone), var(--border-deep) 35%, var(--border-tone) 60%, var(--border-deep));
  }
  .card__panel {
    position: absolute; left: 33px; top: 35px; width: 818px; height: 396px;
    border-radius: 30px;
    background: linear-gradient(90deg, var(--panel-left), var(--panel-mid) 50%, var(--panel-right));
  }
  .rule {
    position: absolute; left: 38px; width: 812px; height: 3px; background: var(--rule);
  }
  .rule--top { top: 98px; }
  .rule--bottom { top: 365px; }
  .ornament {
    position: absolute; left: 398px; width: 76px; height: 36px;
    background: var(--ornament); opacity: .85; border-radius: 38px 38px 6px 6px;
  }
  .ornament--top { top: 62px; }
  .ornament--bottom { top: 370px; border-radius: 6px 6px 38px 38px; }
  .welcome {
    position: absolute; left: 65px; top: 42px; margin: 0;
    font: 400 42px/1 "Great Vibes", cursive; color: var(--light);
  }
  .headline {
    position: absolute; left: 0; right: 0; top: 108px; margin: 0; text-align: center;
    font: 400 35px/1.1 "Crimson Pro", serif; color: var(--light);
  }
  .message {
    position: absolute; left: 30px; right: 30px; top: 158px; margin: 0; text-align: center;
    font: 700 29px/38px "Crimson Pro", serif; color: var(--body-ink);
  }
  .message span { display: block; line-height: 34px; }
  .signoff {
    position: absolute; right: 60px; top: 376px; margin: 0;
    font: 700 25px/1 "Roboto Condensed", sans-serif; color: var(--light);
  }
  .brand-name {
    position: absolute; left: 0; right: 0; top: 130px; margin: 0; text-align: center;
    font: 400 128px/1 "Crimson Pro", serif; color: var(--light);
  }
  .website {
    position: absolute; left: 0; right: 0; top: 402px; margin: 0; text-align: center;
    font: 600 21px/1 "Oswald", sans-serif; color: var(--url-ink); letter-spacing: .5px;
  }
  .social-mark {
    position: absolute; left: 790px; top: 390px; width: 30px; height: 30px;
    background: var(--url-ink); border-radius: 4px;
  }
</style>
</head>
<body>
  <section class="card card--message">
    <div class="card__border" role="img" aria-label="Decorative hexagon pattern border"></div>
    <div class="card__panel"></div>
    <p class="welcome">Welcome</p>
    <div class="ornament ornament--top" role="img" aria-label="Scroll ornament"></div>
    <div class="rule rule--top"></div>
    <h1 class="headline">This is only the beginning</h1>
    <p class="message">
      <span>Your Dorian Vantle bow tie is an adventure for you to unfold,</span>
      <span>unexpected and new.</span>
      Wear it on a night out, or bring a dash of colour to work, dream with it, wear it on a rainy day, create new memories and be surprised.
    </p>
    <div class="rule rule--bottom"></div>
    <div class="ornament ornament--bottom" role="img" aria-label="Scroll ornament"></div>
    <p class="signoff">Dorian Vantle</p>
  </section>

  <section class="card card--brand">
    <div class="card__border" role="img" aria-label="Decorative hexagon pattern border"></div>
    <div class="card__panel"></div>
    <p class="brand-name">Dorian Vantle</p>
    <p class="website">WWW.DORIANVANTLE.EXAMPLE</p>
    <div class="social-mark" role="img" aria-label="Social media links"></div>
  </section>
</body>
</html>
```